High end Electrical/home automation Business Card

Need a card for a high end electrical and home automation company utilising the existing logo.
Phone
Email
Website

Like black look with raised detail. Don’t necessarily need to keep colour of logo it could be made grayscale or white etc

Target Market(s)

High end clients

Contact Information for Business Card

Brightmoor Electrical

Requirements
Must have
• Logo, phone, email, website, address

High end look
Nice to have
• Black background card
Raised font
Should not have
• Lots of colour

```html
<!DOCTYPE html>
<html lang="en">
<head>
<meta charset="utf-8">
<title>Brightmoor Electrical — Business Card</title>
<link rel="stylesheet" href="https://fonts.googleapis.com/css2?family=Archivo:wght@400;800;900&family=Arimo:wght@400;700&display=swap">
<style>
  :root {
    --stage: #2b2c2f;
    --blue: #1596d6;
    --blue-deep: #0b5f8f;
    --charcoal: #2f3336;
    --ink: #222426;
    --paper: #ffffff;
    --rule: #3a3d40;
  }
  * { box-sizing: border-box; margin: 0; padding: 0; }
  html, body { width: 1200px; height: 900px; overflow: hidden; }
  body {
    background: var(--stage);
    font-family: "Arimo", Arial, sans-serif;
    position: relative;
  }
  .card {
    position: absolute;
    left: 232px;
    width: 736px;
    height: 420px;
    border-radius: 26px;
    overflow: hidden;
  }
  /* Front */
  .card--front {
    top: 20px;
    background:
      radial-gradient(ellipse 65% 80% at 45% 50%, var(--blue) 0%, var(--blue-deep) 45%, #1f3340 78%, #33373b 100%);
  }
  .front__brand {
    position: absolute;
    left: 0; right: 0; top: 166px;
    display: flex;
    align-items: center;
    justify-content: center;
    gap: 18px;
    font-family: "Archivo", Arial, sans-serif;
    font-weight: 900;
    font-size: 46px;
    line-height: 56px;
    color: var(--paper);
    letter-spacing: 0.5px;
  }
  .front__dot {
    width: 40px; height: 40px;
    border-radius: 50%;
    background: var(--paper);
    flex: none;
  }
  .front__web {
    position: absolute;
    left: 0; right: 0; top: 248px;
    text-align: center;
    color: var(--paper);
    font-size: 15px;
    letter-spacing: 5px;
  }
  /* Back */
  .card--back {
    top: 460px;
    background: var(--paper);
  }
  .back__brand {
    position: absolute;
    left: 48px; top: 108px;
    display: flex;
    align-items: center;
    gap: 14px;
    font-family: "Archivo", Arial, sans-serif;
    font-weight: 900;
    font-size: 36px;
    line-height: 46px;
    color: var(--charcoal);
  }
  .back__dot {
    width: 34px; height: 34px;
    border-radius: 50%;
    background: var(--blue);
    flex: none;
  }
  .back__person {
    position: absolute;
    right: 52px; top: 40px;
    text-align: right;
  }
  .back__name {
    font-family: "Archivo", Arial, sans-serif;
    font-weight: 800;
    font-size: 27px;
    color: var(--blue);
  }
  .back__title { font-size: 15px; color: var(--ink); margin-top: 2px; }
  .back__address {
    position: absolute;
    right: 52px; top: 196px;
    text-align: right;
    font-size: 18px;
    line-height: 1.25;
    color: var(--ink);
  }
  .back__rule {
    position: absolute;
    left: 48px; right: 52px; top: 252px;
    height: 1.5px;
    background: var(--rule);
  }
  .contact {
    position: absolute;
    left: 48px; top: 284px;
    list-style: none;
  }
  .contact__item {
    display: flex; align-items: center; gap: 14px;
    font-size: 23px; color: var(--ink);
    line-height: 30px;
  }
  .contact__icon { width: 20px; height: 20px; flex: none; }
  .contact__accent { color: var(--blue); }
</style>
</head>
<body>
  <section class="card card--front" aria-label="Card front">
    <p class="front__brand"><span class="front__dot" aria-hidden="true"></span>Brightmoor Electrical</p>
    <p class="front__web">www.brightmoorelectric.com</p>
  </section>

  <section class="card card--back" aria-label="Card back">
    <p class="back__brand"><span class="back__dot" aria-hidden="true"></span>Brightmoor Electrical</p>
    <div class="back__person">
      <p class="back__name">Daniel Hartley</p>
      <p class="back__title">Manager</p>
    </div>
    <p class="back__address">Your address, city<br>state, ZIP 0000</p>
    <div class="back__rule"></div>
    <ul class="contact">
      <li class="contact__item">
        <svg class="contact__icon" viewBox="0 0 24 24" aria-hidden="true"><path fill="#1596d6" d="M6.6 10.8a15.1 15.1 0 0 0 6.6 6.6l2.2-2.2a1 1 0 0 1 1-.25 11.4 11.4 0 0 0 3.6.57 1 1 0 0 1 1 1V20a1 1 0 0 1-1 1A17 17 0 0 1 3 4a1 1 0 0 1 1-1h3.5a1 1 0 0 1 1 1c0 1.25.2 2.450.57 3.57a1 1 0 0 1-.25 1z"/></svg>
        <span>312-555-0148</span>
      </li>
      <li class="contact__item">
        <svg class="contact__icon" viewBox="0 0 24 24" aria-hidden="true"><rect x="2.5" y="5" width="19" height="14" rx="1.5" fill="none" stroke="#1596d6" stroke-width="2"/><path d="M3 6l9 7 9-7" fill="none" stroke="#1596d6" stroke-width="2"/></svg>
        <span>hello@brightmoormail.com</span>
      </li>
      <li class="contact__item">
        <svg class="contact__icon" viewBox="0 0 24 24" aria-hidden="true"><g fill="none" stroke="#1596d6" stroke-width="1.8"><circle cx="12" cy="12" r="9.5"/><ellipse cx="12" cy="12" rx="4" ry="9.5"/><path d="M2.5 12h19M4 7h16M4 17h16"/></g></svg>
        <span>www.<span class="contact__accent">brightmoorelectric</span>.com</span>
      </li>
    </ul>
  </section>
</body>
</html>
```